Business Card Design Project

I require a business card with the following information on them for various different people;
name
m:
f:
e:
I have a logo already and will attached that. We are in the construction industry. I require something clean and simple but eye catching at the same time. You can use another colour with our logo if you like and you can style the logo as well if you wish. I am open.
Also it needs to be front and back design.
Industry/Entity Type
Construction
Requirements
Must have
- Logo, name, mobile, fax and email address.
Front and back design

```html
<!DOCTYPE html>
<html lang="en">
<head>
<meta charset="utf-8">
<title>Harrowfield Developments – Business Cards</title>
<link rel="stylesheet" href="https://fonts.googleapis.com/css2?family=Open+Sans:wght@400;600;700&display=swap">
<style>
  :root {
    --backdrop: #2b2b2d;
    --brand-green: #52b043;
    --card-white: #ffffff;
    --logo-grey: #4a4a4a;
    --text-light: #ffffff;
  }
  * { margin: 0; padding: 0; box-sizing: border-box; }
  html, body {
    width: 1200px;
    height: 944px;
    overflow: hidden;
    background: var(--backdrop);
    font-family: "Open Sans", sans-serif;
  }
  .stage { position: relative; width: 1200px; height: 944px; }

  .card {
    position: absolute;
    width: 580px;
    height: 330px;
    background: var(--brand-green);
    box-shadow: 0 10px 24px rgba(0,0,0,0.45);
    overflow: hidden;
  }
  .card--front { left: 70px; top: 70px; }
  .card--back  { left: 550px; top: 544px; }

  .front-band {
    position: absolute;
    left: 0; right: 0;
    top: 100px;
    height: 130px;
    background: var(--card-white);
    display: flex;
    align-items: center;
    justify-content: center;
  }

  .wordmark {
    display: flex;
    align-items: center;
    gap: 14px;
    color: var(--logo-grey);
    font-weight: 600;
    font-size: 30px;
    letter-spacing: 0.5px;
    white-space: nowrap;
  }
  .wordmark__square {
    width: 34px;
    height: 34px;
    background: var(--brand-green);
    flex: none;
  }

  .back-panel {
    position: absolute;
    left: 0; right: 0; top: 0;
    height: 232px;
    background: var(--brand-green);
    color: var(--text-light);
  }
  .back-footer {
    position: absolute;
    left: 0; right: 0; bottom: 0;
    height: 98px;
    background: var(--card-white);
    display: flex;
    align-items: center;
    padding-left: 36px;
  }

  .holder { position: absolute; left: 34px; top: 30px; }
  .holder__name { font-size: 22px; font-weight: 600; line-height: 1.2; }
  .holder__role { font-size: 13px; font-weight: 600; }

  .contact-list {
    position: absolute;
    left: 350px;
    top: 86px;
    list-style: none;
    font-size: 15px;
    font-weight: 400;
  }
  .contact-list li {
    display: flex;
    align-items: center;
    gap: 10px;
    height: 21px;
  }
  .contact-list li.gap-before { margin-top: 22px; }
  .contact-list svg { width: 14px; height: 14px; flex: none; }
</style>
</head>
<body>
<main class="stage">

  <section class="card card--front" aria-label="Card front">
    <div class="front-band">
      <div class="wordmark">
        <span class="wordmark__square"></span>
        <span class="wordmark__name">Harrowfield Developments</span>
      </div>
    </div>
  </section>

  <section class="card card--back" aria-label="Card back">
    <div class="back-panel">
      <div class="holder">
        <p class="holder__name">Mark Ellison</p>
        <p class="holder__role">manager</p>
      </div>
      <ul class="contact-list">
        <li>
          <svg viewBox="0 0 14 14" aria-hidden="true"><path d="M3 1.5l2.2 2.6-1.2 1.4a8 8 0 0 0 4.5 4.5l1.4-1.2 2.6 2.2-1.3 1.6C7 12.6 1.4 7 1.4 2.8z" fill="#fff"/></svg>
          <span>512-555-0142</span>
        </li>
        <li>
          <svg viewBox="0 0 14 14" aria-hidden="true"><rect x="1" y="6" width="12" height="6" rx="1" fill="#fff"/><rect x="3.5" y="2" width="7" height="4" fill="#fff"/></svg>
          <span>512-555-0143</span>
        </li>
        <li class="gap-before">
          <svg viewBox="0 0 14 14" aria-hidden="true"><rect x="1" y="3" width="12" height="8" rx="1" fill="#fff"/><path d="M1.5 3.5L7 8l5.5-4.5" fill="none" stroke="#52b043" stroke-width="1.2"/></svg>
          <span>info@harrowfield.com</span>
        </li>
        <li>
          <svg viewBox="0 0 14 14" aria-hidden="true"><circle cx="7" cy="7" r="6" fill="#fff"/></svg>
          <span>www.harrowfield.com</span>
        </li>
      </ul>
    </div>
    <div class="back-footer">
      <div class="wordmark">
        <span class="wordmark__square"></span>
        <span class="wordmark__name">Harrowfield Developments</span>
      </div>
    </div>
  </section>

</main>
</body>
</html>
```